Summit Bodyform Gym Website

We need a website design for our gym.

Summit is the UAE's first calisthenics and parkour gym. The theme under which the gym revolves is that one does not require any machinery to workout as our bodies could be themselves the machinery. The gym is designed to be the more of a social hub rather than an "in-and-out" gym, where people come train, have fun, hang out and socialize for a few hours rather than just train for 60 minutes then leave. The gym is designed to be a big open space with lots of natural sunlight, natural wood and plants all over the place to create a natural and refreshing setting. We also use recycled material throughout the gym and recycle our waste as being green is part of our philosophy. We currently also have some of the world's top and most recognized calisthenics athletes working with us.

We would like our website to reflect all that as well as provide a simple, interactive and fun way for visitors to be able to get class and gym information, check out gym media and contact us for bookings.

Target Market(s)

Ages 15-35

Industry/Entity Type

Fitness

Coding

Coded - Design and coding required

Number of Pages Required

4 page

Font styles to use
Decorative

Colors
0792cd

Requirements
Must have
• Class descriptions
• Gym description
• Class schedules
• Trainer profiles
• Gym philosophy
• Contact Details
Nice to have
• A link to contact us directly for a free first trial class

```html
<!DOCTYPE html>
<html lang="en">
<head>
<meta charset="utf-8">
<title>Summit Bodyform Gym</title>
<link href="https://fonts.googleapis.com/css2?family=Oswald:wght@400;500&family=Roboto:wght@400;500;700&display=swap" rel="stylesheet">
<style>
:root{
  --blue:#1a9bc7;
  --blue-deep:#0b6f93;
  --ink:#222;
  --dark:#2b2a2a;
  --footer:#333333;
  --base:#1c1c1c;
  --white:#fff;
}
*{margin:0;padding:0;box-sizing:border-box}
html,body{width:1200px;height:2612px;overflow:hidden}
body{font-family:'Roboto',Arial,sans-serif;color:var(--ink);background:var(--white);position:relative}

/* header */
.site-header{position:relative;height:169px;background:var(--white)}
.brand{position:absolute;left:100px;top:26px;display:flex;align-items:center;gap:12px}
.brand-mark{width:26px;height:26px;border-radius:50%;background:var(--blue)}
.brand-name{font-family:'Oswald',sans-serif;font-weight:500;font-size:38px;color:var(--ink);line-height:1;white-space:nowrap}
.contact-line{position:absolute;left:548px;top:40px;font-size:15px;color:var(--blue);white-space:nowrap}
.contact-line b{font-weight:400;color:var(--ink)}
.contact-line span{margin-right:16px}
.socials{position:absolute;left:968px;top:32px;display:flex;gap:8px}
.socials i{width:28px;height:28px;border-radius:50%;background:var(--blue-deep);display:block}
.main-nav{position:absolute;left:287px;right:0;top:107px;height:58px;background:var(--blue);
  clip-path:polygon(48px 0,100% 0,100% 100%,0 100%);display:flex;align-items:center;padding-left:73px;gap:27px}
.main-nav a{font-family:'Oswald',sans-serif;font-size:13.5px;color:var(--white);text-decoration:none;letter-spacing:.2px;white-space:nowrap}

/* hero */
.hero{position:relative;height:524px;background:linear-gradient(100deg,#6f5a4e 0%,#b98a6c 30%,#8fa7b9 55%,#4f6e8a 75%,#2c3440 100%)}
.hero-caption{position:absolute;left:73px;top:256px;width:331px;height:218px;background:rgba(40,40,40,.72);padding:28px 0 0 30px}
.hero-caption h1{font-family:'Oswald',sans-serif;font-weight:500;color:var(--white);font-size:42px;line-height:1.1}
.hero-caption h2{font-family:'Oswald',sans-serif;font-weight:400;color:var(--white);font-size:28px;line-height:1.2}
.trial-btn{display:inline-block;margin-top:24px;background:var(--blue);color:var(--white);font-family:'Oswald',sans-serif;font-size:20px;padding:13px 17px;text-decoration:none}
.slide-arrow{position:absolute;top:241px;width:34px;height:34px;border-radius:50%;background:rgba(255,255,255,.35)}

/* welcome */
.welcome{height:270px;background:var(--dark);text-align:center;color:var(--white);padding-top:46px}
.welcome h2{font-family:'Oswald',sans-serif;font-weight:400;font-size:38px}
.welcome .sub{font-size:13px;color:#ccc;margin-top:8px;letter-spacing:.3px}
.welcome p.body{width:1000px;margin:24px auto 0;font-size:11.5px;line-height:22px;color:#aaa}

/* services */
.services{height:648px;padding-top:46px}
.section-title{font-family:'Oswald',sans-serif;font-weight:400;font-size:36px;color:var(--blue);text-align:center}
.service-grid{position:absolute;left:99px;top:1092px;width:1002px;display:grid;grid-template-columns:repeat(3,1fr);column-gap:2px;row-gap:19px}
.service-tile{position:relative;height:227px;background:linear-gradient(160deg,#c9d3d9,#6f7e88 60%,#39424a)}
.service-tile.warm{background:linear-gradient(160deg,#c9a27e,#7c6654 60%,#3a3029)}
.service-tile.cool{background:linear-gradient(160deg,#5e8fb8,#2b4e6e 60%,#18263a)}
.service-tile .label{position:absolute;left:22px;bottom:14px;color:var(--white)}
.service-tile h3{font-family:'Roboto',sans-serif;font-weight:700;font-size:16px;text-transform:uppercase}
.service-tile p{font-size:10.5px;margin-top:6px}

/* feature band */
.feature{height:432px;background:linear-gradient(90deg,#0e6a8a,#2a92b3 45%,#157392);text-align:center;color:var(--white);padding-top:98px}
.feature h2{font-family:'Oswald',sans-serif;font-weight:400;font-size:58px;line-height:1}
.feature p{width:920px;margin:26px auto 0;font-size:16px;line-height:28px}
.more-btn{display:inline-block;margin-top:28px;border:2px solid var(--white);color:var(--white);text-decoration:none;font-size:17px;padding:10px 30px}

/* blog */
.blog{position:relative;height:283px}
.blog-title{position:absolute;left:106px;top:38px;font-size:20px;font-weight:500;color:#333;text-transform:uppercase}
.blog-title span{color:var(--blue)}
.blog-nav{position:absolute;left:1083px;top:44px}
.post{position:absolute;top:96px;display:flex;gap:16px;width:480px}
.post-thumb{width:209px;height:142px;border:4px solid #ddd;flex:none;background:linear-gradient(135deg,#2b2b2b,#7a5a4a 50%,#1b1b1b)}
.post-thumb.plates{background:linear-gradient(135deg,#0f0f0f,#5a5a5a 50%,#111)}
.post h4{font-size:13px;font-weight:700;color:#222;margin-top:14px}
.post .date{font-size:10.5px;color:var(--blue);margin-top:8px}
.post p{font-size:10px;line-height:18px;color:#666;margin-top:8px}
.post a{display:block;font-size:11px;color:var(--blue);text-decoration:none;margin-top:6px}

/* footer */
.site-footer{position:relative;height:221px;background:var(--footer);color:#ddd}
.col{position:absolute;top:38px}
.col h5{font-size:14px;font-weight:500;color:var(--white);text-transform:uppercase;margin-bottom:20px}
.col p,.col li{font-size:11px;line-height:18px;color:#ccc}
.col ul{list-style:none}
.col li{margin-bottom:5px}
.col li::before{content:"\25B8";margin-right:6px;font-size:9px}
.col .gap{margin-top:14px}
.news-form{display:flex;margin-top:14px}
.news-form .field{width:138px;height:30px;background:var(--white);color:#888;font-size:10px;padding:9px 10px}
.news-form .go{width:61px;height:30px;background:var(--blue);color:var(--white);font-size:11px;text-align:center;line-height:30px}
.foot-social{display:flex;gap:14px;margin-top:18px}
.foot-social i{width:31px;height:31px;border:1px solid #bbb;border-radius:50%;display:block}
.base{height:65px;background:var(--base);color:var(--white);font-size:11px;text-align:center;line-height:65px}
</style>
</head>
<body>

<header class="site-header">
  <div class="brand"><span class="brand-mark"></span><span class="brand-name">Summit Bodyform Gym</span></div>
  <div class="contact-line"><span>CALL US : <b>555 . 210. 4839</b></span><span>EMAIL : <b>info@sbgym.example</b></span></div>
  <div class="socials"><i></i><i></i><i></i><i></i></div>
  <nav class="main-nav">
    <a href="#">HOME</a><a href="#">CLASS DESCRIPTIONS</a><a href="#">GYM DESCRIPTION</a><a href="#">CLASS SCHEDULES</a><a href="#">TRAINER PROFILES</a><a href="#">GYM PHILOSOPHY</a><a href="#">CONTACT</a>
  </nav>
</header>

<section class="hero" role="img" aria-label="Athlete doing push-ups on kettlebells in a bright gym">
  <span class="slide-arrow" style="left:36px"></span>
  <span class="slide-arrow" style="right:36px"></span>
  <div class="hero-caption">
    <h1>SUMMIT</h1>
    <h2>BODYFORM GYM</h2>
    <a class="trial-btn" href="#">FREE FIRST TRIAL CLASS</a>
  </div>
</section>

<section class="welcome">
  <h2>WELCOME TO SUMMIT</h2>
  <p class="sub">NEQUE PORRO QUISQUAM EST QUI DOLOREM IPSUM QUIA DOLOR</p>
  <p class="body">Lorem Ipsum has been the industry's standard dummy text ever since the 1500s, when an unknown printer took a galley of type and scrambled it to make a type specimen book. It has survived not only five centuries, but also the leap into electronic typesetting, remaining essentially unchanged. It was popularised in the 1960s with the release of Typeset sheets containing Lorem Ipsum passages, and more recently with desktop layout tools including versions of Lorem Ipsum.</p>
</section>

<section class="services">
  <h2 class="section-title">OUR SERVICES</h2>
  <div class="service-grid">
    <div class="service-tile" role="img" aria-label="Open training floor with pull-up rigs"><div class="label"><h3>Class Descriptions</h3><p>NEQUE PORRO QUISQUAM EST QUI DOLOREM IPSUM</p></div></div>
    <div class="service-tile warm" role="img" aria-label="Gym hall with mats and wood floor"><div class="label"><h3>Gym Description</h3><p>NEQUE PORRO QUISQUAM EST QUI DOLOREM IPSUM</p></div></div>
    <div class="service-tile cool" role="img" aria-label="Gymnastic rings hanging from a rig"><div class="label"><h3>Class Schedules</h3><p>NEQUE PORRO QUISQUAM EST QUI DOLOREM IPSUM</p></div></div>
    <div class="service-tile warm" role="img" aria-label="Wooden wall with plants and dumbbell rack"><div class="label"><h3>Trainer Profiles</h3><p>NEQUE PORRO QUISQUAM EST QUI DOLOREM IPSUM</p></div></div>
    <div class="service-tile" role="img" aria-label="Wide gym with training structures"><div class="label"><h3>Gym Philosophy</h3><p>NEQUE PORRO QUISQUAM EST QUI DOLOREM IPSUM</p></div></div>
    <div class="service-tile cool" role="img" aria-label="Training rig and equipment racks"><div class="label"><h3>Calisthenics Gym</h3><p>NEQUE PORRO QUISQUAM EST QUI DOLOREM IPSUM</p></div></div>
  </div>
</section>

<section class="feature" role="img" aria-label="Gym interior in blue tint">
  <h2>SUMMIT BODYFORM GYM</h2>
  <p>Lorem Ipsum has been the industry's standard dummy text ever since the 1500s, when an unknown printer took a galley of type and scrambled it to make a type specimen book. It has survived not only five centuries, but also the leap into electronic typesetting, remaining essentially unchanged. It was popularised in the 1960s with the release of Typeset sheets containing Lorem Ipsum passages, and more recently with desktop layout tools including versions of Lorem Ipsum.</p>
  <a class="more-btn" href="#">VIEW MORE</a>
</section>

<section class="blog">
  <h2 class="blog-title">Latest <span>Blog</span></h2>
  <svg class="blog-nav" width="22" height="14" viewBox="0 0 22 14"><path d="M7 2 2 7l5 5M15 2l5 5-5 5" fill="none" stroke="#333" stroke-width="2"/></svg>
  <article class="post" style="left:106px">
    <div class="post-thumb" role="img" aria-label="Athlete with boxing gloves"></div>
    <div><h4>SIMPLY DUMMY TEXT</h4><div class="date">21-sep-2015</div>
    <p>Lorem Ipsum has been the industry's standard dummy text ever since the 1500s, when an unknown printer took a galley of type and scrambled it to make a type specimen book. It has survived not only five centuries, but also popularised.</p>
    <a href="#">Read More &gt;&gt;</a></div>
  </article>
  <article class="post" style="left:623px">
    <div class="post-thumb plates" role="img" aria-label="Barbell and weight plates on dark floor"></div>
    <div><h4>SIMPLY DUMMY TEXT</h4><div class="date">21-sep-2015</div>
    <p>Lorem Ipsum has been the industry's standard dummy text ever since the 1500s, when an unknown printer took a galley of type and scrambled it to make a type specimen book. It has survived not only five centuries, but also popularised.</p>
    <a href="#">Read More &gt;&gt;</a></div>
  </article>
</section>

<footer class="site-footer">
  <div class="col" style="left:101px;width:240px">
    <h5>Text Widget</h5>
    <p>BrightFrame helps you to quickly and easily build incredible websites with an open site builder.</p>
    <p class="gap">Proin gravida nibh vel velit auctor aliquet. Aenean sollicitudin, lorem quis bibendum auctor, nisi elit consequat ipsum, nec sagittis.</p>
  </div>
  <div class="col" style="left:432px">
    <h5>Links</h5>
    <ul><li>Customer Support</li><li>Documentation</li><li>Resources</li><li>General FAQs</li><li>Shortcodes</li></ul>
  </div>
  <div class="col" style="left:626px">
    <h5>Get In Touch</h5>
    <p>Address : 18 Cedar Court,<br>Harbor Point</p>
    <p class="gap">Phone : 555.318.2046</p>
    <p class="gap">Email : info@sbgym.example</p>
  </div>
  <div class="col" style="left:902px;width:210px">
    <h5>Newsletter</h5>
    <p>Your about us information would fit here nicely.</p>
    <div class="news-form"><div class="field">Email address</div><div class="go">Submit</div></div>
    <div class="foot-social"><i></i><i></i><i></i></div>
  </div>
</footer>
<div class="base">Copyright © 2015. All Rights Reserved</div>

</body>
</html>
```